Inspirational Quotes Poster Set

Brookloft is a stylish coworking space, which has a design-oriented vintage look from the 60's with an industrial touch (www.brookloft-example.com) Brookloft Quote Poster Set of 16 posters. The poster should be typo oriented and rather simple. Reflecting a bit the clean billboard design from the sixties. Minimal / simple graphical elements

Target Market(s)

Startups and Entrepreneurs

Industry/Entity Type

Startup

Font styles to use
Sans Serif

Colors

Designer to choose colors to be used in the design.

Requirements
Must have
• Posters need to be on and very stylish

```html
<!DOCTYPE html>
<html lang="en">
<head>
<meta charset="utf-8">
<title>Brookloft Quote Poster Set – Never Gives Up</title>
<link href="https://fonts.googleapis.com/css2?family=Bebas+Neue&family=Carlito&display=swap" rel="stylesheet">
<style>
  :root {
    --poster-red: #b44b54;
    --icon-tone: #c76a72;
    --ink: #ffffff;
  }
  html, body {
    margin: 0;
    padding: 0;
    width: 738px;
    height: 1200px;
    overflow: hidden;
    background: var(--poster-red);
  }
  .poster {
    position: relative;
    width: 738px;
    height: 1200px;
    background: var(--poster-red);
    color: var(--ink);
    overflow: hidden;
  }
  .emblem {
    position: absolute;
    left: 0;
    top: 0;
    width: 738px;
    height: 320px;
  }
  .quote-line {
    position: absolute;
    left: 0;
    width: 738px;
    margin: 0;
    text-align: center;
    font-family: "Bebas Neue", "Oswald", sans-serif;
    font-weight: 400;
    line-height: 1;
    white-space: nowrap;
  }
  .quote-line--small { font-size: 84px; letter-spacing: 1px; }
  .quote-line--large { font-size: 147px; letter-spacing: 2px; }
  .line-1 { top: 345px; }
  .line-2 { top: 446px; }
  .line-3 { top: 546px; }
  .line-4 { top: 644px; }
  .line-5 { top: 796px; }
  .attribution {
    position: absolute;
    left: 0;
    width: 738px;
    margin: 0;
    text-align: center;
    font-family: "Carlito", "Calibri", sans-serif;
    font-size: 42px;
    line-height: 1;
    white-space: nowrap;
  }
  .attribution-name { top: 1055px; }
  .attribution-role { top: 1108px; }
</style>
</head>
<body>
  <main class="poster">
    <svg class="emblem" viewBox="0 0 738 320" aria-hidden="false">
      <circle cx="364" cy="181" r="119" fill="none" stroke="var(--ink)" stroke-width="5"/>
      <rect x="305" y="93" width="127" height="173" rx="18" fill="var(--icon-tone)"
            role="img" aria-label="Line icon of a raised clenched fist"/>
    </svg>

    <p class="quote-line quote-line--small line-1">It’s hard to</p>
    <p class="quote-line quote-line--small line-2">beat a person</p>
    <p class="quote-line quote-line--small line-3">who</p>
    <p class="quote-line quote-line--large line-4">NEVER</p>
    <p class="quote-line quote-line--large line-5">GIVES UP.</p>

    <p class="attribution attribution-name">Rube Hartley</p>
    <p class="attribution attribution-role">Baseball Legend</p>
  </main>
</body>
</html>
```